Location-Based project

I need a webdesign for a project similar to bramblenet, tiparno or kelvik. The feel should be more like bramblenet.
An example of the content of the site can be found on http://www.varquist.nl/maddox/site
The idea of the project is searching and performing actions based on the real location of your mobile phone.
There will also be an Duvix/Quelbran app developed.

Reason: Good things, take time :-)

Reason: I am still waiting for some design to be submitted

```html
<!DOCTYPE html>
<html lang="en">
<head>
<meta charset="utf-8">
<title>maddox – location based search</title>
<link href="https://fonts.googleapis.com/css2?family=Arimo:wght@400;700&display=swap" rel="stylesheet">
<style>
:root{
  --sky-top:#8fd3ef;
  --sky-mid:#c4eaf8;
  --sky-low:#f3f7e6;
  --bar:#7cc3df;
  --panel:rgba(255,255,255,.35);
  --panel-line:rgba(255,255,255,.75);
  --white:#ffffff;
  --cyan:#2cc0e6;
  --pink:#e8659f;
  --ink:#333333;
  --ink-soft:#555555;
  --star:#f4b400;
  --star-off:#d5d5d5;
  --link:#6fc7e5;
  --scene-top:#f6f1d6;
  --scene-mid:#b9c99a;
  --scene-low:#9d93c2;
}
*{box-sizing:border-box;margin:0;padding:0}
html,body{width:986px;height:1200px;overflow:hidden}
body{
  position:relative;
  font-family:"Arimo",Arial,sans-serif;
  color:var(--ink);
  background:linear-gradient(180deg,var(--sky-top) 0,var(--sky-mid) 420px,#e3f4f7 700px,var(--sky-low) 900px,#fdf8df 990px);
}
.topbar{position:absolute;left:0;top:0;width:986px;height:27px;background:var(--bar);border-bottom:1px solid #6bb4d0}
.topbar .user{position:absolute;left:134px;top:8px;font-size:10px;font-weight:700;color:#e8f6fb}
.topbar .user b{color:#3fe0f5}
.social{position:absolute;right:125px;top:2px;display:flex;gap:6px}
.social span{width:21px;height:21px;border-radius:4px;background:#5a8fb0;display:block}
.social span:nth-child(3){background:#c8393b}
.social span:nth-child(5){background:#3d5f9e}

.brand{position:absolute;left:133px;top:72px;display:flex;align-items:center;gap:12px}
.brand .mark{width:56px;height:56px;border-radius:8px;background:#3a8fd0}
.brand .name{font-size:38px;font-weight:700;color:var(--pink);letter-spacing:1px}

.search{position:absolute;left:452px;top:87px;width:398px;height:47px;border-radius:8px;background:rgba(255,255,255,.55);border:1px solid var(--panel-line);padding:6px}
.search .inner{display:flex;align-items:center;gap:6px;height:100%;background:#fff;border-radius:6px;padding:0 6px}
.search svg{flex:none}
.select,.field{height:19px;border:1px solid #bbb;background:linear-gradient(#fff,#ececec);font-size:7px;color:#555;display:flex;align-items:center;padding-left:6px;position:relative}
.select{width:76px}
.select::after{content:"";position:absolute;right:5px;top:7px;border:3px solid transparent;border-top-color:#555}
.field{flex:1;background:#fff}
.field .go{position:absolute;right:0;top:0;width:20px;height:17px;border-left:1px solid #bbb;background:#eee}

.feed{position:absolute;left:125px;top:155px;width:728px;height:432px;border-radius:10px;background:var(--panel);border:2px solid var(--panel-line)}
.post{position:absolute;background:var(--white);border:1px solid #b9c7cf;border-radius:6px;padding:8px 10px 9px 56px;font-size:10px;font-weight:700;line-height:13px;color:var(--ink)}
.post::after{content:"";position:absolute;bottom:-9px;left:30px;border:8px solid transparent;border-top-color:#fff;border-bottom:0}
.post p{text-align:center}
.post .avatar{position:absolute;left:10px;top:11px;width:39px;height:39px;background:linear-gradient(#b88b6a,#6c7f6e)}
.post h3{font-size:12px;line-height:15px;color:var(--cyan);margin-bottom:1px}
.post.right{padding:8px 56px 9px 10px;text-align:right}
.post.right::after{left:auto;right:30px}
.post.right .avatar{left:auto;right:10px;background:linear-gradient(#8b4a3a,#d6c3b5)}
.post.right h3{display:flex;justify-content:flex-end;align-items:center;gap:12px}
.stars{display:flex}
.p1{left:16px;top:17px;width:503px}
.p2{left:95px;top:97px;width:612px}
.p3{left:14px;top:176px;width:612px}
.p4{left:14px;top:260px;width:612px}
.p5{left:94px;top:340px;width:612px}

.location{position:absolute;left:125px;top:608px;width:728px;height:367px;background:var(--white);border-radius:6px}
.location h2{position:absolute;left:18px;top:12px;font-size:14px;color:var(--cyan)}
.map{position:absolute;left:0;top:37px;width:463px;height:292px;background:linear-gradient(135deg,#e9e5dc,#d9d3c4 55%,#aac6e0)}
.footer-links{position:absolute;left:20px;top:343px;display:flex;gap:12px;font-size:9px;color:var(--link)}
.side{position:absolute;left:482px;top:38px;width:227px}
.tabs{display:flex;border:1px solid #c6c6c6;height:27px}
.tabs span{flex:1;font-size:9px;color:#555;display:flex;align-items:center;justify-content:center;background:linear-gradient(#fbfbfb,#e8e8e8);border-left:1px solid #c6c6c6}
.tabs span:first-child{border-left:0}
.tabs .active{background:linear-gradient(#e2e2e2,#d0d0d0)}
.side h1{margin-top:12px;font-size:36px;line-height:42px;letter-spacing:3px;color:var(--pink);font-weight:700}
.side .lead{margin-top:12px;font-size:13.5px;line-height:22px;font-weight:700;color:var(--cyan)}
.side .body{margin-top:10px;font-size:10.5px;line-height:19.5px;color:var(--ink-soft);height:117px;overflow:hidden}
.subscribe{position:absolute;left:486px;top:338px;display:flex;gap:13px}
.subscribe .input{width:139px;height:18px;border:1px solid #aaa}
.subscribe .btn{height:18px;padding:0 9px;border-radius:3px;background:linear-gradient(#5fdcf3,#1fb3d6);color:#fff;font-size:10px;font-weight:700;display:flex;align-items:center}

.scene{position:absolute;left:0;top:990px;width:986px;height:210px;background:linear-gradient(180deg,var(--scene-top) 0,var(--scene-mid) 55%,var(--scene-low) 100%)}
</style>
</head>
<body>
<header class="topbar">
  <div class="user"><b>Hello</b> - Lena Corvell</div>
  <nav class="social" aria-label="Social networks"><span></span><span></span><span></span><span></span><span></span><span></span></nav>
</header>

<div class="brand"><span class="mark"></span><span class="name">maddox</span></div>

<form class="search">
  <div class="inner">
    <svg width="26" height="26" viewBox="0 0 26 26"><circle cx="15" cy="10" r="7" fill="none" stroke="#aaa" stroke-width="2"/><line x1="10" y1="15" x2="3" y2="23" stroke="#aaa" stroke-width="3" stroke-linecap="round"/></svg>
    <div class="select">Selector</div>
    <div class="select">Selector</div>
    <div class="field">Enter your search here...<span class="go"></span></div>
  </div>
</form>

<svg width="0" height="0" style="position:absolute"><defs><path id="star" d="M6.5 0l2 4.3 4.5.5-3.4 3 1 4.6-4.1-2.4-4.1 2.4 1-4.6L0 4.8l4.5-.5z"/></defs></svg>

<section class="feed">
  <article class="post p1"><div class="avatar" role="img" aria-label="User photo"></div><h3>Save the World</h3><p>Phasellus molestie magna non est bibendum non venenatis nisl tempor. Suspendisse dictum feugiat nisl ut dapibus. Mauris iaculis porttitor posuere. Praesent id metus</p></article>
  <article class="post right p2"><div class="avatar" role="img" aria-label="User photo"></div><h3><span class="stars"><svg width="80" height="13" viewBox="0 0 80 13"><g fill="var(--star)"><use href="#star"/><use href="#star" x="17"/><use href="#star" x="34"/></g><g fill="var(--star-off)"><use href="#star" x="51"/><use href="#star" x="68"/></g></svg></span>Save the World</h3><p>Phasellus molestie magna non est bibendum non venenatis nisl tempor. Suspenisse dictum feugiat nisl ut dapibus. Mauris iaculis porttitor posuere. Praesent id metus massa, ut blandit odio. Proin quis tortor orci.</p></article>
  <article class="post p3"><div class="avatar" role="img" aria-label="User photo"></div><h3>Save the World</h3><p>Phasellus molestie magna non est bibendum non venenatis nisl tempor. Suspenisse dictum feugiat nisl ut dapibus. Mauris iaculis porttitor posuere. Praesent id metus massa, ut blandit odio. Proin quis tortor orci.</p></article>
  <article class="post p4"><div class="avatar" role="img" aria-label="User photo"></div><h3>Save the World</h3><p>Phasellus molestie magna non est bibendum non venenatis nisl tempor. Suspenisse dictum feugiat nisl ut dapibus. Mauris iaculis porttitor posuere. Praesent id metus massa, ut blandit odio. Proin quis tortor orci.</p></article>
  <article class="post right p5"><div class="avatar" role="img" aria-label="User photo"></div><h3><span class="stars"><svg width="80" height="13" viewBox="0 0 80 13"><g fill="var(--star)"><use href="#star"/><use href="#star" x="17"/><use href="#star" x="34"/></g><g fill="var(--star-off)"><use href="#star" x="51"/><use href="#star" x="68"/></g></svg></span>Save the World</h3><p>Phasellus molestie magna non est bibendum non venenatis nisl tempor. Suspenisse dictum feugiat nisl ut dapibus. Mauris iaculis porttitor posuere. Praesent id metus massa, ut blandit odio. Proin quis tortor orci.</p></article>
</section>

<section class="location">
  <h2>Your location</h2>
  <div class="map" role="img" aria-label="Street map of the city centre with a location pin"></div>
  <nav class="footer-links"><span>About Us</span><span>Contact Blog</span><span>Status</span><span>Goodies</span><span>API Business</span><span>Help</span><span>Jobs</span><span>Terms</span><span>Privacy</span><span>Sitemap</span></nav>
  <div class="side">
    <div class="tabs"><span>First menu</span><span class="active">Active menu</span><span>Third menu</span></div>
    <h1>Welcome</h1>
    <p class="lead">This will be a short introduction to the website, this is only an example &amp; can be changed.</p>
    <p class="body">Lorem Ipsum is simply dummy text of the printing and typesetting industry. Lorem Ipsum has been the industry's standard printer took a galley of type and scrambled it to typesetting, remaining essentially unchanged.remaining essentially unchanged.remaining essentially</p>
  </div>
  <div class="subscribe"><span class="input"></span><span class="btn">Confirm it!</span></div>
</section>

<div class="scene" role="img" aria-label="Illustrated landscape of green hills at sunrise turning to a purple night with a small house"></div>
</body>
</html>
```